Heron Property Inspection business card

I am the principal inspector of Heron Property Inspections. I serve Northern Virginia from Winchester to Arlington.Associate, Federated Guild of Dwelling Examiners (FGDE)Graduate, FGDE Home Inspectors CourseNational Association of Home Inspectors ExamI'd like the business card to look more professional than comical.I pulled the attached picture off the web. I'd like to have something like that or an image of a house as my logo on the cards.

Target Market(s)

Persons who recently purchased a home.

Industry/Entity Type

Business

Contact Information for Business Card

Bob AllenBadger Home Inspections, LLC.4455 River RoadBluemont, Virginia 20135cell: 703-231-6680e-mail: tkmarlow@postvale.net

Font styles to use
Serif
Sans Serif

Requirements
Must have
• I'd like to have a logo, something that identifies me as a home inspector. The attached images are something that I'd like to have incorporated into my business card logo.
Nice to have
• I'd like a sketch of a house and/or a magnifying glass showing a house being inspected. The attached images are used as a suggestion only, I do not own the images.
Should not have
• Gimmicky stuff. I want to appear professional and trustworthy.

```html
<!DOCTYPE html>
<html lang="en">
<head>
<meta charset="utf-8">
<title>Heron Property Inspections – Business Card</title>
<link rel="stylesheet" href="https://fonts.googleapis.com/css2?family=Marcellus&display=swap">
<style>
  :root {
    --backdrop: #e9e7e2;
    --card: #ffffff;
    --ink: #2a2322;
    --brown: #3a2524;
    --green: #2e9e44;
    --green-light: #7cc451;
    --green-deep: #13883d;
  }
  * { box-sizing: border-box; margin: 0; padding: 0; }
  html, body {
    width: 1200px; height: 818px; overflow: hidden;
    background: var(--backdrop);
    font-family: "Marcellus", Georgia, serif;
  }
  .canvas {
    width: 1200px; height: 818px;
    display: flex; align-items: center; justify-content: center;
  }
  .card {
    position: relative;
    width: 1000px; height: 571px;
    background: var(--card);
    box-shadow: 0 10px 30px rgba(0,0,0,.18);
    overflow: hidden;
  }
  .card__swoosh { position: absolute; inset: 0; }
  .brand {
    position: absolute; left: 90px; top: 90px;
    display: flex; align-items: center; gap: 18px;
  }
  .brand__square { width: 28px; height: 28px; background: var(--green); }
  .brand__name {
    color: var(--green-deep);
    font-size: 36px; line-height: 1.15;
    text-transform: uppercase; letter-spacing: .5px;
  }
  .contact {
    position: absolute; right: 80px; top: 110px;
    text-align: right; color: var(--ink);
    font-size: 32px; line-height: 1.35;
  }
  .contact__address { margin-bottom: 28px; }
  .contact__line { display: flex; align-items: center; justify-content: flex-end; gap: 14px; }
  .contact__icon { width: 24px; height: 24px; flex: none; }
  .holder {
    position: absolute; left: 50px; bottom: 40px;
    color: #fff;
  }
  .holder__name { font-size: 34px; line-height: 1.1; }
  .holder__role { font-size: 20px; opacity: .92; margin-top: 4px; }
</style>
</head>
<body>
<main class="canvas">
  <article class="card">
    <svg class="card__swoosh" viewBox="0 0 1000 571" aria-hidden="true">
      <defs>
        <linearGradient id="swooshGreen" x1="0" y1="0" x2="1" y2="1">
          <stop offset="0" stop-color="#4fb33f"/>
          <stop offset=".55" stop-color="#8fd06e"/>
          <stop offset="1" stop-color="#1f9a45"/>
        </linearGradient>
      </defs>
      <path d="M0,250 C180,420 520,520 900,571 L0,571 Z" fill="url(#swooshGreen)"/>
      <path d="M0,200 C180,370 520,480 1000,548 C520,492 180,388 0,222 Z" fill="var(--brown)"/>
    </svg>

    <div class="brand">
      <span class="brand__square"></span>
      <span class="brand__name">Heron Property<br>Inspections, LLC.</span>
    </div>

    <div class="contact">
      <p class="contact__address">7182 Quarry Lane<br>Fernhill, Virginia 20148</p>
      <p class="contact__line">703-555-0192
        <svg class="contact__icon" viewBox="0 0 24 24" aria-hidden="true"><rect x="6" y="2" width="12" height="20" rx="2" fill="var(--green)"/><rect x="8" y="5" width="8" height="11" fill="#fff"/></svg>
      </p>
      <p class="contact__line">tkmarlow@postvale.net
        <svg class="contact__icon" viewBox="0 0 24 24" aria-hidden="true"><rect x="2" y="5" width="20" height="14" fill="var(--green)"/><path d="M2,5 L12,13 L22,5" fill="none" stroke="#fff" stroke-width="1.6"/></svg>
      </p>
    </div>

    <div class="holder">
      <p class="holder__name">Employee Name</p>
      <p class="holder__role">Managing Director</p>
    </div>
  </article>
</main>
</body>
</html>
```